TLK Electricial Contracting Services

Hi guys, after a design for my small electrical company, have logo design files to be incorporated into the layout, the basic concept is electrical contracting services for residential, commercial, industrial & data services, image is clean clear and strong,

Card format is to have a nice clean logo on front,with maybe the Residential – commercial – industrial - data, followed with licensed & insured, followed by contact details on backside of the card.

Target Market(s)

Residential, commercial, industrial sectors.

Industry/Entity Type

Electrical

Contact Information for Business Card

TLK logo,
Residential – commercial – industrial - data
REC: 61307
Email: tlk@vornamail.net.au
Phone: 0487 352 019

Requirements
Must have
• Clean & strong design.
Nice to have
• If possible, I would like the logo colours inverted so the text is orange and the background is black on the front of the card, then the backside of the card be the reverse colour
Should not have
• No Sparks, lightning bolts,

```html
<!DOCTYPE html>
<html lang="en">
<head>
<meta charset="UTF-8">
<title>TLK Electrical – Business Card</title>
<link href="https://fonts.googleapis.com/css2?family=Lato:wght@400;700&display=swap" rel="stylesheet">
<style>
  :root {
    --backdrop: #3a332f;
    --card-black: #1c1c1c;
    --card-black-deep: #141414;
    --brand-orange: #f0821e;
    --text-white: #f2f2f2;
    --logo-silver: #c9c9c9;
    --divider: rgba(255, 255, 255, 0.06);
  }
  * { box-sizing: border-box; margin: 0; padding: 0; }
  html, body {
    width: 1200px;
    height: 844px;
    overflow: hidden;
    background: var(--backdrop);
    font-family: "Lato", Arial, sans-serif;
  }
  .stage {
    width: 1200px;
    height: 844px;
    display: flex;
    align-items: center;
    justify-content: center;
    gap: 60px;
  }
  .card {
    position: relative;
    width: 525px;
    height: 300px;
    border-radius: 4px;
    background: linear-gradient(135deg, var(--card-black) 0%, var(--card-black-deep) 100%);
    box-shadow: 0 14px 30px rgba(0, 0, 0, 0.45);
    overflow: hidden;
  }

  /* Contact side */
  .card--contact { display: flex; }
  .brand-block {
    width: 250px;
    display: flex;
    flex-direction: column;
    justify-content: center;
    align-items: center;
    padding-top: 40px;
    border-right: 1px solid var(--divider);
  }
  .brand-mark {
    font-weight: 700;
    font-size: 72px;
    line-height: 1;
    letter-spacing: -1px;
    color: var(--brand-orange);
  }
  .brand-name {
    margin-top: 4px;
    font-weight: 700;
    font-size: 13px;
    color: var(--brand-orange);
  }
  .contact-block {
    flex: 1;
    padding: 36px 16px 0 22px;
    color: var(--text-white);
    font-size: 14px;
    line-height: 1.3;
  }
  .person-name {
    color: var(--brand-orange);
    font-size: 19px;
  }
  .person-role { margin-bottom: 14px; }
  .sectors { margin-bottom: 4px; }
  .licence { margin-bottom: 14px; }
  .licence-label { color: var(--brand-orange); }
  .contact-list { list-style: none; }
  .contact-label {
    color: var(--brand-orange);
    display: inline-block;
    width: 22px;
  }

  /* Logo side */
  .card--logo {
    display: flex;
    flex-direction: column;
    align-items: center;
    justify-content: center;
  }
  .card--logo .brand-mark { color: var(--logo-silver); }
  .card--logo .brand-name { color: var(--logo-silver); }
</style>
</head>
<body>
  <main class="stage">
    <section class="card card--contact" aria-label="Business card, contact side">
      <div class="brand-block">
        <span class="brand-mark">TLK</span>
        <span class="brand-name">Tyler Lane Electrical</span>
      </div>
      <div class="contact-block">
        <p class="person-name">Daniel Harper</p>
        <p class="person-role">Managing Director</p>
        <p class="sectors">Residential – Commercial –<br>Industrial – Data</p>
        <p class="licence">Licensed &amp; Insured · <span class="licence-label">REC:</span> 61307</p>
        <ul class="contact-list">
          <li><span class="contact-label">T:</span>0487 352 019</li>
          <li><span class="contact-label">E:</span>tlk@vornamail.net.au</li>
          <li><span class="contact-label">W:</span>www.tylerlane.net.au</li>
        </ul>
      </div>
    </section>

    <section class="card card--logo" aria-label="Business card, logo side">
      <span class="brand-mark">TLK</span>
      <span class="brand-name">Tyler Lane Electrical</span>
    </section>
  </main>
</body>
</html>
```